Poster & Flyer - Golf Tournament

Poster and Flyer (2 sperapate) is required for an upcoming Torvenne Classic Golf Tournament. Although this tournament is amongst friends only (normally 40 people) we want to announce this years (13th year) tournament a bit differently.

* Poster should grab the players (brief outline)
* Flyer should have more detail and graphics
* Design flows in each Poster/Flyer.

There are several components to the Tournament that include:

1. Tournament Logo
2. Prizes (Set of golf clubs and Hotel Accommodation)
3. FairwayLogix App (Live leaderboard)
4. Timetable of events and golf
5. Venue of Golf Tournament
6. Payment terms

All information relating to components are attached.

1. Tournament Logo - Some brief background, The "Torvenne" was religious compass like symbol that basically pointed the people in the right direction when they were being faithful. We have incorporated the Logo with a golf tournament :-).

2. 1st Prize - full set of Fitted Harrier ZEN Flux Max Golf Clubs with ZEN Golf Bag (Worth $2, 200 RRP)

2nd Prize - 2 nights 5 Star Accommodation at any Brenmore Hotel in Australia includes Breakfast. (Worth $700 RRP).

Fairway Logix is a free mobile Golf app that will take the Torvenne Classic to another level.

Easy mobile live scoring, leaderboards, chat, stats & social interactions - all real time with all popular game formats.

Bring it On!

More info go to http://www.fairwaylogix.example/

* Can you incorporate some graphics from website in Poster and Flyer.

4. Timetable document attached. Make it presentable on the Flyer.

5. If we can incorporate aspects (graphics) of the golf course e.g. Golf Course Logo's, signature holes etc.

Go to:

a. Tamblin Vale Course - http://www.tamblinvale.example.au
b. Mount Orrin Golf Resort - https://www.vtma.example.au/wps/wcm/connect/vtma/Resorts/VTMA+Resorts/VTMA+Mount+Orrin+Resort/Mount+Orrin+Golf

If you go to findora images I'm sure you can find further images relating to the golf course.

6. Payment terms: Can you please express the "early bird special"

Also I will need a extra poster without the "early bird special" once the time runs out.

If you have any further questions please do not hesitate to drop me an email.

* Please note - I will end Project early if I find a design I desire.
Updates

Please add "Like us on chatterbook" logo (see attached)

chatterbook link is - http://www.chatterbook.example/Torvenneclassic

```html
<!DOCTYPE html>
<html lang="en">
<head>
<meta charset="utf-8">
<title>Torvenne Classic Golf Tournament</title>
<link href="https://fonts.googleapis.com/css2?family=Raleway:wght@300;400;500;600;700;800&display=swap" rel="stylesheet">
<style>
:root{
  --green:#3f8a1f;
  --green-dark:#2c6a12;
  --grey:#6b6b6b;
  --grey-dark:#4a4a4a;
  --ball:#f4f4f4;
  --ball-shade:#d9d9d9;
  --gold:#b8913a;
  --navy:#1d2f9c;
  --ink:#1a1a1a;
  --badge:#3b5998;
}
*{margin:0;padding:0;box-sizing:border-box}
html,body{width:848px;height:1200px;overflow:hidden;background:#fff}
body{font-family:"Raleway",Arial,sans-serif;color:var(--grey)}
.poster{position:relative;width:848px;height:1200px;overflow:hidden;background:#fff}
.course-photo{position:absolute;left:0;top:0;width:848px;height:1200px;
  background:linear-gradient(180deg,#7fb2e4 0%,#b9d6ef 18%,#5d8a3a 30%,#3f7d22 42%,#c8a27a 48%,#4f9a2a 56%,#c9a37e 66%,#3e8a1e 74%,#2f6f14 100%)}
.ball-panel{position:absolute;left:0;top:0}
.abs{position:absolute}
.circle{position:absolute;border-radius:50%}
.ball-circle{background:radial-gradient(circle at 60% 40%,#ffffff 0%,var(--ball) 55%,var(--ball-shade) 100%);box-shadow:0 2px 6px rgba(0,0,0,.25)}
.like-badge{left:28px;top:15px;width:68px;height:24px;display:flex;align-items:center;gap:4px;background:#eef1f7;border:1px solid #b6bfd3;border-radius:3px;padding:0 4px;font-size:7.5px;line-height:8.5px;font-weight:700;color:var(--badge)}
.like-badge .dot{flex:none;width:8px;height:8px;background:var(--badge)}
.page-link{left:104px;top:20px;font-size:12px;color:var(--grey-dark);white-space:nowrap}
.page-link b{font-weight:700}
.event-date{left:18px;top:92px;font-size:25px;line-height:25px;text-transform:uppercase;font-weight:400;color:var(--grey)}
.event-date .hl{color:var(--green);font-weight:700;font-size:21px}
.event-date .small{font-size:14px;text-transform:none}
.event-title{left:240px;top:160px;font-size:33px;line-height:34px;font-weight:500;color:var(--grey-dark)}
.event-title .arrow{display:inline-block;vertical-align:middle;margin-right:6px}
.early-bird{left:198px;top:236px;width:266px;height:50px;background:linear-gradient(180deg,#5aa82c,#2f7412);color:#fff;font-size:25px;font-weight:400;display:flex;align-items:center;justify-content:center;box-shadow:0 3px 5px rgba(0,0,0,.3)}
.early-bird b{font-weight:800}
.terms{left:200px;top:304px;width:268px;font-size:13px;line-height:23.5px;font-weight:400;color:var(--grey-dark)}
.terms .price{color:var(--green);font-weight:600}
.terms .note{font-size:6.3px;line-height:9px;color:var(--green-dark);margin-top:6px;white-space:nowrap}
.price-tag{left:16px;top:372px;font-weight:500;color:var(--green-dark);text-align:center;width:110px}
.price-tag .only{font-size:40px;line-height:40px}
.price-tag .amount{font-size:37px;line-height:40px;font-weight:800;color:var(--grey)}
.price-tag .amount small{font-size:22px}
.sponsor{left:232px;top:512px;display:flex;align-items:center;gap:8px;font-size:22px;font-weight:800;color:var(--ink)}
.sponsor .mark{width:18px;height:18px;border-radius:50%;background:var(--ink)}
.app-circle{left:-46px;top:566px;width:200px;height:200px;background:radial-gradient(circle at 50% 30%,#3a3a3a,#0d0d0d 70%);box-shadow:0 2px 6px rgba(0,0,0,.35)}
.app-name{left:12px;top:654px;font-size:21px;font-weight:700;color:#fff}
.app-tag{left:12px;top:680px;font-size:9.5px;font-weight:600;color:#66c23a}
.app-features{left:218px;top:640px;width:230px;text-align:center;font-size:12.6px;line-height:19px;color:var(--grey-dark);font-weight:500}
.app-features b{color:var(--green);font-weight:800}
.app-link{left:220px;top:680px;width:230px;height:24px;background:var(--green-dark);color:#fff;font-size:13.5px;display:flex;align-items:center;justify-content:center}
.bags-photo{left:250px;top:720px;width:186px;height:186px;border:4px solid #fff;background:linear-gradient(120deg,#1b1b1b 0%,#24357a 40%,#e9e9e9 60%,#e0661f 100%);box-shadow:0 2px 6px rgba(0,0,0,.3)}
.first-prize{left:54px;top:800px;color:var(--grey-dark)}
.prize-rank{font-size:27px;line-height:27px;font-weight:400;color:var(--green)}
.prize-name{font-size:33px;line-height:33px;font-weight:800;color:var(--grey)}
.prize-detail{font-size:9px;font-weight:500;color:var(--grey-dark);margin-top:2px}
.club-photo{left:120px;top:874px;width:44px;height:44px;border:1px solid #999;background:radial-gradient(circle,#e8e8e8,#bcbcbc)}
.hotel-circle{left:16px;top:946px;width:172px;height:172px;background:#fff;border:5px solid #9a9a9a}
.hotel-mark{left:89px;top:988px;width:26px;height:26px;border-radius:50%;background:var(--navy)}
.hotel-name{left:16px;top:1030px;width:172px;text-align:center;font-size:31px;font-weight:600;color:var(--navy)}
.second-prize{left:212px;top:1018px}
.second-prize .prize-detail{font-size:9.5px}
.contact{left:55px;top:1145px;font-size:12.6px;color:var(--grey-dark)}
.contact-phone{left:66px;top:1162px;display:flex;align-items:center;gap:10px;font-size:14px;font-weight:700;color:var(--ink)}
.contact-phone svg{display:block}
.event-logo{left:570px;top:150px;width:260px;text-align:center;color:var(--gold);font-size:30px;font-weight:700;letter-spacing:2px;text-transform:uppercase;line-height:34px}
.event-logo .mark{width:58px;height:58px;border-radius:50%;background:var(--gold);margin:0 auto 12px}
</style>
</head>
<body>
<main class="poster">
  <div class="course-photo" role="img" aria-label="Photograph of a golf course with trees, sand bunkers, a flag on the green and a golfer playing out of a bunker"></div>

  <svg class="ball-panel" width="848" height="1200" viewBox="0 0 848 1200" aria-hidden="true">
    <defs>
      <radialGradient id="ballShade" cx="0.2" cy="0.5" r="0.9">
        <stop offset="0" stop-color="#ffffff"/>
        <stop offset="0.75" stop-color="#f2f2f2"/>
        <stop offset="1" stop-color="#cfcfcf"/>
      </radialGradient>
    </defs>
    <path d="M0 0 H405 C560 180 640 420 585 640 C540 860 420 1060 275 1200 H0 Z" fill="url(#ballShade)"/>
    <g fill="none" stroke="#8a8a8a" stroke-width="1.4" stroke-dasharray="7 6">
      <path d="M150 180 C200 230 200 300 160 345"/>
      <path d="M150 450 C200 500 200 560 160 600"/>
      <path d="M150 690 C200 700 230 730 250 760"/>
      <path d="M260 900 C220 930 190 950 168 968"/>
    </g>
    <g fill="#8a8a8a">
      <path d="M153 340 l10 2 -8 7z"/>
      <path d="M153 595 l10 2 -8 7z"/>
      <path d="M246 752 l8 10 -10 -1z"/>
      <path d="M164 960 l10 3 -10 6z"/>
    </g>
    <g fill="#7d7d7d">
      <path d="M48 258 h16 l-8 48z"/>
      <path d="M48 518 h16 l-8 48z"/>
      <path d="M48 766 h16 l-8 48z"/>
    </g>
  </svg>

  <div class="abs like-badge"><span class="dot"></span><span>Like us on<br>chatterbook</span></div>
  <div class="abs page-link">www.chatterbook.example/<b>Torvenneclassic</b></div>

  <div class="circle ball-circle" style="left:-60px;top:50px;width:215px;height:215px"></div>
  <div class="abs event-date">
    Tuesday<br><span class="hl">5TH</span> <span class="small">to</span><br>Thursday<br><span class="hl">7TH</span><br>November<br><span class="hl">2013</span>
  </div>

  <h1 class="abs event-title">
    <svg class="arrow" width="26" height="26" viewBox="0 0 26 26"><circle cx="13" cy="13" r="12" fill="#4a4a4a"/><path d="M6 13 h10 M12 8 l5 5 -5 5" stroke="#fff" stroke-width="3" fill="none"/></svg>GOLF<br>TOURNAMENT
  </h1>
  <div class="abs early-bird"><b>EARLY</b>&nbsp;BIRD PRICE</div>
  <div class="abs terms">
    <p>a)&nbsp;&nbsp; Get a <span class="price">$65</span> savings when you pay the total of <span class="price">$530</span> upfront before 15th July 2013</p>
    <p>b)&nbsp;&nbsp; or Pay <span class="price">$300</span> before the 30th June to secure your place. The remaining <span class="price">$295</span> to be paid before the 30th Sept.</p>
    <p class="note">*Due to individual cancellations we can only refund money if someone replaces your spot.</p>
  </div>

  <div class="circle ball-circle" style="left:-60px;top:305px;width:220px;height:220px"></div>
  <div class="abs price-tag"><div class="only">ONLY</div><div class="amount">595<small>$</small></div></div>

  <div class="abs sponsor"><span class="mark"></span>Stridecat Golf</div>

  <div class="circle app-circle"></div>
  <div class="abs app-name">Fairway Logix</div>
  <div class="abs app-tag">Sharing the golf experience</div>
  <div class="abs app-features">LIVE <b>LEADERBOARD</b> SCORING<br><b>LIVE CHAT</b> WITH OTHER GOLFERS</div>
  <div class="abs app-link">www.fairwaylogix.example</div>

  <div class="circle bags-photo" role="img" aria-label="Photo of three golf bags in black, blue, white and orange"></div>
  <div class="abs first-prize">
    <div class="prize-rank">1ST PLACE</div>
    <div class="prize-name">FULL SET</div>
    <div class="prize-detail">Fitted Harrier ZEN Flux Max Golf Clubs</div>
  </div>
  <div class="circle club-photo" role="img" aria-label="Photo of a golf iron club head"></div>

  <div class="circle hotel-circle"></div>
  <div class="circle hotel-mark"></div>
  <div class="abs hotel-name">Brenmore</div>
  <div class="abs second-prize">
    <div class="prize-rank">2ND PLACE</div>
    <div class="prize-name">5* HOTEL</div>
    <div class="prize-detail">INCLUDING BREAKFAST</div>
  </div>

  <div class="abs contact">Contact Dale if any questions</div>
  <div class="abs contact-phone">
    <svg width="20" height="20" viewBox="0 0 20 20"><rect width="20" height="20" rx="4" fill="#3f8a1f"/><path d="M6 4 l3 3 -1.5 2 c1 2 2 3 3.5 3.5 l2 -1.5 3 3 -2 2 c-5 0 -10 -5 -10 -10z" fill="#fff"/></svg>
    0400 555 218
  </div>

  <div class="abs event-logo"><div class="mark"></div>Torvenne Classic</div>
</main>
</body>
</html>
```